House Cleaning Platform for Consumers and Cleaners

UPDATE: I've attached screenshots showing a purchase flow example, something all designers have missed in their designs. PLEASE check the URLs I've included in the brief for examples of a cleaning website. I've seen mostly landing pages and nothing else.

WHAT I'M LOOKING FOR:
I need the UI designed for a house cleaning web platform from 2 separate experiences: one from the consumer end to order a cleaner to come clean their house and one from a cleaner’s end that manages their orders and manages their schedule.

The UI will need to include photo uploading for before and after photos, a checkout/cart experience w/ tips, toggle options for adding and removing rooms/extras cleaning add-ons, customer+cleaner reviews (meaning the cleaner finished the job and they can rate and review the customer as well as the customer can rate and review the cleaner), order history for consumers, job history for cleaners, profile, settings, and landing pages for both.

PLEASE DO NOT USE THE COLOR BLUE AS THE PRIMARY COLOR. Use a light green (HEX #2fdf86) instead for primary theming color.

REFERENCES:
If you'd like a few websites I've enjoyed for references, checkout:
larkpolish.example, vomby.example, and brightfernhome.example.

For sake of branding, the company name is PlumNest. Currently do not have a logo as we have not decided on the name. Logo will come later.

Feel free to reach out to me if you have any questions!
Updates

Most designer submissions were a landing page and only a landing page. Very few designed the flows I requested and none designed a schedule management page. I even updated the Brief to more clearly outline the needs and references. Only about 2-3 of the designers actually did more than a landing page. Still don't believe I received 6 designers input that I had paid for.

Target Market(s)

FULL-TIME WORKING HOUSEHOLDS, SINGLE PROFESSIONALS, SINGLE PARENTS, ELDERLY & MOBILITY CHALLENGED, BUSY BODIES.

Industry/Entity Type

Cleaning, gig work.

Number of Pages Required

5+ page

Font styles to use
Other font styles liked:
• Jost or Lexend are great Google Font options I've used in the pitch deck and horribly done app mockups.

Colors
00AB8E
00BBA5
67D7C9
C6EFE9
E9F9F6
59FF00
82FF00
B8FF75
E3FFCB
F4FFEA
FFF300
FFF600
FEFA6F
FFFEC7
FFFEE8
FFC000
F8CF3A
FAE287
FDF2CF
FEFAEE

Requirements
Must have
• Landing page, consumer flow, cleaner schedule management, checkout flow, Rate & Review for consumer and/or cleaner, order history, profile.
Nice to have
• I'd like it to be simple in design and modern, but not so simple it's boring. Iconography can sometimes break that up, but I don't want it looking busy. It's a cleaning platform so the UI should look clean.

```html
<!DOCTYPE html>
<html lang="en">
<head>
<meta charset="utf-8">
<title>PlumNest – Book Your Services</title>
<link href="https://fonts.googleapis.com/css2?family=Lexend:wght@300;400;500&family=Noto+Sans:wght@500;600;700&display=swap" rel="stylesheet">
<style>
:root{
  --green:#22d384;
  --orange:#f7931e;
  --ink:#111;
  --text:#444;
  --muted:#b5b5b5;
  --line:#d8d8d8;
  --border:#cfcfcf;
}
*{box-sizing:border-box;margin:0;padding:0}
html,body{width:1200px;height:998px;overflow:hidden;background:#fff}
body{font-family:'Lexend',sans-serif;color:var(--ink);position:relative}
.header{position:absolute;top:20px;left:101px;right:101px;height:50px;display:flex;align-items:center}
.brand{font-family:'Noto Sans',sans-serif;font-weight:700;font-size:30px;color:var(--green);letter-spacing:-.3px}
.nav{display:flex;gap:19px;margin-left:auto;font-size:12px;font-weight:400}
.search{margin-left:32px;width:219px;height:26px;border:1px solid var(--line);border-radius:13px;display:flex;align-items:center;padding-left:8px;font-size:12px;gap:14px}
.login{margin-left:31px;font-size:12px}
.signup{margin-left:12px;background:var(--green);border-radius:13px;height:25px;width:75px;display:flex;align-items:center;justify-content:center;font-size:11px}
h1{position:absolute;top:128px;width:100%;text-align:center;font-family:'Noto Sans',sans-serif;font-weight:700;font-size:37px}
.steps{position:absolute;top:209px;left:154px;width:892px;height:26px}
.steps .track{position:absolute;top:12px;left:12px;right:12px;height:2px;background:var(--line)}
.steps .dot{position:absolute;top:0;width:25px;height:25px;border-radius:50%;border:2px solid var(--line);background:#fff}
.steps .dot.active{border-color:var(--orange)}
.field{position:absolute;width:469px;border-top:3px solid var(--green)}
.field h2{font-family:'Noto Sans',sans-serif;font-weight:500;font-size:19px;margin-top:10px}
.field p{font-size:11.5px;font-weight:300;color:var(--text);line-height:18px;margin-top:14px}
.field p b{font-weight:500;color:#222}
.input{margin-top:20px;height:38px;border:1px solid var(--border);display:flex;align-items:center;padding:0 18px;font-size:11.5px;font-weight:300;color:var(--muted);justify-content:space-between}
.radios{display:flex;margin-top:22px;font-size:12px;font-weight:400;gap:0}
.radio{display:flex;align-items:center;gap:13px;margin-right:30px}
.radio i{width:13px;height:13px;border-radius:50%;border:1px solid var(--line);display:block}
.radio i.on{border:3.5px solid var(--green)}
.btn{position:absolute;top:837px;width:175px;height:50px;border-radius:25px;display:flex;align-items:center;justify-content:center;font-size:16px;font-weight:400}
.back{left:101px;border:1px solid var(--border)}
.next{left:307px;background:var(--green)}
</style>
</head>
<body>
<header class="header">
  <div class="brand">PlumNest</div>
  <nav class="nav"><span>Home</span><span>Pricing</span><span>Services</span><span>Contact</span><span>Help</span></nav>
  <div class="search"><svg width="14" height="14" viewBox="0 0 14 14"><circle cx="6" cy="6" r="5" fill="none" stroke="#222" stroke-width="1.2"/><line x1="9.7" y1="9.7" x2="13" y2="13" stroke="#222" stroke-width="1.2"/></svg>Search</div>
  <span class="login">Login</span>
  <span class="signup">Sign Up</span>
</header>

<h1>Book Your Services Now</h1>

<div class="steps">
  <div class="track"></div>
  <div class="dot active" style="left:0"></div>
  <div class="dot" style="left:124px"></div>
  <div class="dot" style="left:248px"></div>
  <div class="dot" style="left:371px"></div>
  <div class="dot" style="left:495px"></div>
  <div class="dot" style="left:619px"></div>
  <div class="dot" style="left:743px"></div>
  <div class="dot" style="left:867px"></div>
</div>

<section class="field" style="left:101px;top:296px">
  <h2>Enter Property Zip Code</h2>
  <p>The zip code helps us to pull accurate quote and pricing details.</p>
  <div class="input">Zip Code</div>
</section>
<section class="field" style="left:630px;top:296px">
  <h2>Total Square Feet At Home</h2>
  <p>Enter your total square feet of your home. This number will be verified by our system.</p>
  <div class="input">Square Footage</div>
</section>
<section class="field" style="left:101px;top:472px">
  <h2>How Many Bedrooms?</h2>
  <p>Enter total number of bedrooms in the home. You can Exclude number of Bedrooms at a later step.</p>
  <div class="input">Select Bedrooms<svg width="12" height="7" viewBox="0 0 12 7"><path d="M0 0h12L6 7z" fill="#111"/></svg></div>
</section>
<section class="field" style="left:630px;top:472px">
  <h2>How Many Bathrooms?</h2>
  <p>Enter total number of bathrooms in the home. <b>Round half baths up</b> (this will not affect price). You can Exclude Bedrooms at a later step.</p>
  <div class="input">Select Bathhrooms<svg width="12" height="7" viewBox="0 0 12 7"><path d="M0 0h12L6 7z" fill="#111"/></svg></div>
</section>
<section class="field" style="left:101px;top:666px">
  <h2>Any Pets At Home?</h2>
  <p>This include any cats or dogs that live in or spend time in the same home. Select any one.</p>
  <div class="radios">
    <label class="radio"><i class="on"></i>No pets in the home</label>
    <label class="radio"><i></i>Dog(s)</label>
    <label class="radio"><i></i>Cats(s)</label>
    <label class="radio" style="margin-right:0"><i></i>Dog(s) and Cats(s)</label>
  </div>
</section>

<a class="btn back">Back</a>
<a class="btn next">Save &amp; Next</a>
</body>
</html>
```